Redesign Of Current Landing Page

I need to redesign this landing page https://www.brightlanepromo.biz/?page=landing&landing=23 (Please do not opt in because when you do it will show you the home page. Please clear your cookies before going to this url above to view the 1 page landing page.)

Please use my updated website as a reference for colors and logo.
http://sitecradlewerk.com/dh/bpq/index.html

I would like the call to action to be a button that opens into a lead form...

Button would be "Download Samples"

Target Market(s)

small business owners

Industry/Entity Type

Marketing

Number of Pages Required

1 page

Colors

Designer to choose colors to be used in the design.

Requirements
Must have
• must be full responsive on all devices
Nice to have
• must have a legitimate professional apeal to it
Should not have
• open

```html
<!DOCTYPE html>
<html lang="en">
<head>
<meta charset="utf-8">
<title>Brightlane Promo Quest – Landing</title>
<link rel="stylesheet" href="https://fonts.googleapis.com/css2?family=Roboto:wght@400;500;700&family=Open+Sans:wght@400&display=swap">
<style>
:root{
  --blue:#1572bb;
  --blue-deep:#0f3e6a;
  --grey-btn:#8f9194;
  --icon:#7a7a7a;
  --text:#333;
  --muted:#555;
  --white:#fff;
}
*{margin:0;padding:0;box-sizing:border-box}
html,body{width:948px;height:1200px;overflow:hidden;background:var(--white)}
body{position:relative;font-family:'Roboto',sans-serif;color:var(--text)}
.abs{position:absolute}

.site-header{left:0;top:0;width:948px;height:71px}
.brand{left:95px;top:18px;display:flex;align-items:center;gap:8px}
.brand-dot{width:28px;height:28px;border-radius:50%;background:var(--blue)}
.brand-name{font-weight:700;font-size:24px;color:var(--blue-deep);letter-spacing:1px}
.btn{background:var(--grey-btn);color:var(--white);font-weight:500;border-radius:4px;display:flex;align-items:center;justify-content:center}
.btn-email{left:714px;top:20px;width:155px;height:34px;font-size:16px}

.hero{left:0;top:71px;width:948px;height:396px;overflow:hidden}
.hero-photo{position:absolute;inset:0;background:linear-gradient(90deg,#1472bd 0%,#1472bd 30%,#4a86bf 45%,#c9cfd6 62%,#e8e2dc 78%,#b08f7c 100%)}
.hero-title{left:105px;top:106px;font-size:29px;font-weight:700;color:var(--white)}
.hero-sub{left:105px;top:150px;font-size:20px;line-height:24px;color:var(--white);width:320px}
.btn-download{left:108px;top:224px;width:175px;height:34px;font-size:16px}
.slide-nav{top:301px;width:32px;height:32px;border-radius:50%;background:var(--blue-deep);display:flex;align-items:center;justify-content:center}

.section-title{left:0;width:948px;text-align:center;font-size:18px;font-weight:700;color:var(--blue)}
.benefits{left:74px;top:555px;width:792px;display:flex}
.benefit{width:132px;text-align:center}
.benefit svg{height:32px;width:40px;display:block;margin:0 auto 26px}
.benefit p{font-size:9px;line-height:12px;color:var(--text)}

.tab-active{left:328px;top:685px;width:104px;height:46px;background:var(--blue);color:var(--white);font-size:18px;font-weight:700;display:flex;align-items:center;justify-content:center}
.tab{left:455px;top:685px;height:46px;font-size:18px;font-weight:700;color:var(--blue);display:flex;align-items:center}
.tab-panel{left:78px;top:731px;width:792px;height:158px;background:var(--blue);padding:40px 49px 0;color:var(--white);font-size:9.6px;line-height:11.5px}
.tab-panel p{margin-bottom:11px}

.quote-mark{left:453px;top:946px;width:42px;height:42px;border-radius:50%;background:var(--icon);display:flex;align-items:center;justify-content:center}
.quote-text{left:150px;top:994px;width:648px;text-align:center;font-size:10px;line-height:20.4px;color:var(--muted)}
.quote-nav{top:1013px}
.author{left:0;width:948px;text-align:center;font-size:12px;font-weight:700}
.author-name{top:1096px;color:var(--blue)}
.author-place{top:1116px;color:var(--grey-btn)}

.site-footer{left:0;top:1155px;width:948px;height:45px;background:var(--grey-btn);color:var(--white);font-family:'Open Sans',sans-serif;font-size:11px;display:flex;align-items:center;justify-content:center}
</style>
</head>
<body>

<header class="abs site-header">
  <div class="abs brand"><span class="brand-dot"></span><span class="brand-name">BPQ</span></div>
  <a class="abs btn btn-email">Email Us Samples</a>
</header>

<section class="abs hero">
  <div class="hero-photo" role="img" aria-label="Photo of three colleagues reviewing paperwork at a desk, toned blue on the left"></div>
  <h1 class="abs hero-title">Attract more customers</h1>
  <p class="abs hero-sub">who spend more money with your business more often!</p>
  <a class="abs btn btn-download">Download Samples</a>
  <span class="abs slide-nav" style="left:107px"><svg width="10" height="14" viewBox="0 0 10 14"><path d="M7 2 2 7l5 5" stroke="#fff" stroke-width="1.8" fill="none"/></svg></span>
  <span class="abs slide-nav" style="left:148px"><svg width="10" height="14" viewBox="0 0 10 14"><path d="M3 2l5 5-5 5" stroke="#fff" stroke-width="1.8" fill="none"/></svg></span>
</section>

<h2 class="abs section-title" style="top:499px">WHY OFFER INCENTIVES TO CUSTOMERS?</h2>

<div class="abs benefits">
  <div class="benefit">
    <svg viewBox="0 0 40 32"><g fill="var(--icon)"><rect x="6" y="26" width="4" height="4"/><rect x="12" y="22" width="4" height="8"/><rect x="18" y="18" width="4" height="12"/><rect x="24" y="10" width="4" height="20"/><rect x="30" y="2" width="4" height="28"/></g></svg>
    <p>Increase Responses From Your Existing Ads</p>
  </div>
  <div class="benefit">
    <svg viewBox="0 0 40 32"><path d="M30 3a7 7 0 0 0-8 9L9 25a2.5 2.5 0 0 0 4 4l13-13a7 7 0 0 0 9-8l-4 4-4-1-1-4z" fill="var(--icon)"/></svg>
    <p>#1.Sales Closing Tool - Gift w/ Purchase</p>
  </div>
  <div class="benefit">
    <svg viewBox="0 0 40 32"><path d="M20 1l4.7 10 10.8 1.2-8 7.3 2.3 10.7L20 24.6 10.2 30.2l2.3-10.7-8-7.3L15.3 11z" fill="var(--icon)"/></svg>
    <p>Build Brand Awareness and Trust</p>
  </div>
  <div class="benefit">
    <svg viewBox="0 0 40 32"><g fill="var(--icon)"><circle cx="11" cy="8" r="5"/><circle cx="29" cy="8" r="5"/><circle cx="20" cy="11" r="6"/><path d="M3 24c0-6 4-9 8-9s6 2 6 2v7z"/><path d="M37 24c0-6-4-9-8-9s-6 2-6 2v7z"/><path d="M9 32c0-8 5-13 11-13s11 5 11 13z"/></g></svg>
    <p>Insure The Sale Over Your Competition</p>
  </div>
  <div class="benefit">
    <svg viewBox="0 0 40 32"><g fill="var(--icon)"><path d="M4 10h24V5l8 7-8 7v-5H4z"/><path d="M36 22H12v-5l-8 7 8 7v-5h24z"/></g></svg>
    <p>Boost Repeat and Referral Business-</p>
  </div>
  <div class="benefit">
    <svg viewBox="0 0 40 32"><rect x="3" y="5" width="34" height="22" rx="1" fill="none" stroke="var(--icon)" stroke-width="3"/><path d="M3 10a5 5 0 0 0 5-5M37 10a5 5 0 0 1-5-5M3 22a5 5 0 0 1 5 5M37 22a5 5 0 0 0-5 5" stroke="var(--icon)" stroke-width="2" fill="none"/><circle cx="20" cy="16" r="6" fill="var(--icon)"/><path d="M19 13.5l1.5-1v7" stroke="#fff" stroke-width="1.6" fill="none"/></svg>
    <p>Improve Retention Rates</p>
  </div>
</div>

<div class="abs tab-active">IMAGINE</div>
<div class="abs tab">HOW CAN WE DO IT?</div>
<div class="abs tab-panel">
  <p>Being able to create exciting give away promotions that will boost your sales without ever having to worry about cost.</p>
  <p>Brightlane Promo Quest, Inc. provides high-perceived value promotional incentives to businesses that want to advertise an exciting Give Away that will instantly attract more customers from your existing advertising efforts.</p>
  <p>Your business can give away incentive certificates that are redeemable for luxury hotel &amp; resort stays with airfare included, cruises, cash for gas, groceries, dining and even electronic goods.</p>
</div>

<h2 class="abs section-title" style="top:920px">TESTIMONIALS</h2>
<div class="abs quote-mark"><svg width="22" height="18" viewBox="0 0 22 18"><g fill="#fff"><path d="M1 2h8v8c0 4-2 6-6 7l-1-2c2-1 3-2 3-4H1z"/><path d="M12 2h8v8c0 4-2 6-6 7l-1-2c2-1 3-2 3-4h-4z"/></g></svg></div>
<p class="abs quote-text">I began using your incentives two years ago to boost lead generation efforts. I have experienced a 63% increase in lead captures. And, even more importantly, my sales have increased as well. The ability to offer unlimited certificates and not having to pay for each certificate I give away is perhaps the best feature of the program, but having the flexibility to email or print certificates for my customers is also wonderful. I even use your html banners to automate my promotions right on my website!,</p>
<svg class="abs quote-nav" style="left:115px" width="12" height="18" viewBox="0 0 12 18"><path d="M9 2 3 9l6 7" stroke="#999" stroke-width="1.6" fill="none"/></svg>
<svg class="abs quote-nav" style="left:825px" width="12" height="18" viewBox="0 0 12 18"><path d="M3 2l6 7-6 7" stroke="#999" stroke-width="1.6" fill="none"/></svg>
<p class="abs author author-name">Dana R.</p>
<p class="abs author author-place">Ashford, KY</p>

<footer class="abs site-footer">© 2017 Brightlane Promo Quest, Inc. - All Rights Reserved</footer>

</body>
</html>
```